New design for Giftwell Hub Website - landing page plus 3 carousel pages

We have a new website we want to launch for 501c3 organizations - Faith-based organizations, not for profit organizations, colleges and universities. Note - this is a design only project. We want to see designs for the landing page and the 3 other pages - Faith-based organizations, not for profit organizations, colleges and universities.
Format: We expect to create this website in Wix so requirement is to make the graphics Wix compatible
See Dossier attached for more details, 4 wireframes (1 landing page and 3 carousel pages), and brand guidelines
Please be creative and and make the visuals engaging. We do NOT want you to simply replicate what is in the wireframe. We are looking for a totally new, fresh and engaging design.
Number of Pages Required
1 page
Look and feel
Each slider illustrates characteristics of the customer's brand and the style your logo design should communicate.

```html
<!DOCTYPE html>
<html lang="en">
<head>
<meta charset="utf-8">
<title>Giftwell Hub – 501c3 Organizations</title>
<link href="https://fonts.googleapis.com/css2?family=Lexend:wght@300;400;500;600&display=swap" rel="stylesheet">
<style>
:root{
  --navy:#0a1a35;
  --navy-deep:#071429;
  --ink:#0d1b3a;
  --green:#2fc48c;
  --teal:#1f8f86;
  --blue:#0b2c9e;
  --blue-link:#1f3fae;
  --grey-box:#ecedef;
  --muted:#4a4f5c;
  --white:#ffffff;
}
*{box-sizing:border-box;margin:0;padding:0}
html,body{width:1200px;height:4874px;overflow:hidden}
body{position:relative;font-family:"Lexend",sans-serif;color:var(--ink);background:var(--white)}
.abs{position:absolute}
.center{text-align:center;left:0;width:1200px}
.btn{position:absolute;background:var(--blue);color:var(--white);border-radius:28px;font-size:18px;display:flex;align-items:center;justify-content:center;font-weight:300}

/* nav */
.nav{top:0;left:0;width:1200px;height:116px;background:var(--white)}
.brand{left:75px;top:30px;display:flex;align-items:center;gap:10px;font-size:28px;font-weight:600;color:var(--navy)}
.brand-dot{width:44px;height:44px;border-radius:50%;border:5px solid var(--teal)}
.nav-links{left:386px;top:52px;display:flex;gap:42px;font-size:15px;font-weight:500;color:var(--navy)}
.nav-links .active{color:var(--blue-link)}

/* hero */
.hero-bg{top:116px;left:0;width:1200px;height:720px;background:linear-gradient(160deg,#11305a 0%,var(--navy) 45%,#060f22 100%)}
.hero-title{top:232px;font-size:62px;color:var(--white);font-weight:400;letter-spacing:1px}
.hero-sub{top:318px;font-size:25px;color:var(--white);font-weight:300;line-height:36px}
.org{width:240px;text-align:center;color:var(--white);font-size:18px;line-height:26px;font-weight:300}
.org-ring{width:160px;height:160px;border-radius:50%;margin:0 auto 20px;background:conic-gradient(var(--blue) 0 25%,var(--green) 25% 50%,transparent 50%);padding:10px;position:relative;left:12px}
.org-ring span{display:block;width:130px;height:130px;border-radius:50%;background:var(--white);position:relative;left:-12px;top:5px}

/* process */
.h2{font-size:50px;font-weight:400;color:var(--ink)}
.step{width:328px;height:135px;background:var(--grey-box);border-radius:40px;padding:14px 28px}
.step h3{font-size:25px;font-weight:400;color:var(--blue-link);margin-bottom:8px}
.step p{font-size:14px;line-height:24px;color:var(--muted);font-weight:300}

/* donation */
.dark{background:var(--navy)}
.amount{width:208px;height:75px;border:2px solid var(--white);border-radius:14px;color:var(--white);font-size:36px;font-weight:500;display:flex;align-items:center;justify-content:center}
.pay-box{left:398px;top:2118px;width:404px;height:104px;border:3px solid #c7cbd2;border-radius:6px;display:flex;align-items:flex-end;justify-content:center;gap:12px;padding-bottom:14px}
.pay-name{position:absolute;top:-18px;left:20px;background:var(--navy);padding:0 10px;color:#5f9be0;font-size:28px;font-weight:600}
.card{width:84px;height:46px;border-radius:6px;background:var(--white);color:var(--navy);font-size:15px;font-weight:500;display:flex;align-items:center;justify-content:center}

/* options */
.option{width:420px;height:188px;border:5px solid var(--teal);border-top-width:4px;border-radius:14px;display:flex;align-items:center;padding-left:12px;gap:20px}
.option .ico{width:130px;height:130px;border-radius:50%;background:#e5e8ec}
.option h4{font-size:24px;font-weight:400;line-height:32px;color:var(--ink)}
.option small{font-size:14px;color:var(--muted);display:block;margin-top:4px}
.option .mini{font-size:16px;font-weight:600;color:var(--navy);margin-top:8px;display:flex;align-items:center;gap:6px}
.option .mini i{width:22px;height:22px;border-radius:50%;border:3px solid var(--teal)}

/* video */
.video{left:143px;top:2940px;width:899px;height:505px;border-radius:36px;border:6px solid var(--white);background:linear-gradient(135deg,#4b5c70,#7c8c9a 50%,#3a4a5e);overflow:hidden}
.play{left:552px;top:3150px;width:76px;height:76px;border-radius:50%;border:4px solid var(--white)}

/* enroll */
.feat{width:300px;text-align:center}
.feat-ring{width:170px;height:170px;border-radius:50%;margin:0 auto 30px;background:conic-gradient(var(--blue) 0 30%,var(--green) 30% 50%,transparent 50% 55%,var(--navy) 55% 95%,transparent 95%);padding:12px}
.feat-ring span{display:block;width:146px;height:146px;border-radius:50%;background:#eef4f6}
.feat h3{font-size:26px;font-weight:400;color:var(--blue-link);margin-bottom:12px}
.feat p{font-size:17px;line-height:26px;color:var(--muted);font-weight:300}

/* newsletter */
.email{left:254px;top:4393px;width:691px;height:67px;border-radius:34px;background:var(--white);border:3px solid #dfe3ea}
.email span{position:absolute;left:28px;top:22px;font-size:15px;color:var(--navy)}
.send{left:764px;top:4399px;width:174px;height:55px;font-size:24px}
.fine{font-size:12.5px;color:var(--white);font-weight:300;line-height:28px}

/* footer */
.footer{top:4652px;left:0;width:1200px;height:222px;background:var(--navy-deep)}
.foot-links{top:4712px;display:flex;justify-content:center;gap:42px;font-size:15px;color:var(--white)}
.copy{top:4750px;font-size:13px;color:var(--white);font-weight:300}
.social{top:4788px;display:flex;justify-content:center;gap:18px;font-size:13px;color:var(--white)}
</style>
</head>
<body>

<header class="abs nav">
  <div class="abs brand"><span class="brand-dot"></span>Ledgerleaf</div>
  <nav class="abs nav-links">
    <span class="active">HOME</span><span>ABOUT US</span><span>NEWSROOM</span><span>PATENTS</span><span>CLIENTS</span><span>FAQ</span><span>CONTACT</span>
  </nav>
</header>

<section>
  <div class="abs hero-bg" role="img" aria-label="Dark blue technology background with faint digital circuitry"></div>
  <svg class="abs" style="top:680px;left:0" width="1200" height="180" viewBox="0 0 1200 180">
    <path d="M0 80 C200 150 400 40 650 120 C850 180 1000 60 1200 60 L1200 180 L0 180Z" fill="var(--green)"/>
    <path d="M0 40 C200 160 420 60 650 140 C860 200 1020 80 1200 70 L1200 180 L0 180Z" fill="#2a55c8" opacity=".85"/>
    <path d="M0 110 C220 140 420 90 640 150 C860 200 1020 110 1200 110 L1200 180 L0 180Z" fill="var(--white)"/>
  </svg>
  <h1 class="abs center hero-title">501c3 ORGANIZATION</h1>
  <p class="abs center hero-sub">Lorem ipsum dolor sit amet, consectetur adipiscing elit, sed do eiusmod<br>tempor incididunt ut labore et dolore magna aliqua.</p>
  <div class="abs org" style="left:243px;top:436px"><div class="org-ring"><span role="img" aria-label="Plant growing from hand icon"></span></div>Non Profit<br>Organisation</div>
  <div class="abs org" style="left:485px;top:436px"><div class="org-ring"><span role="img" aria-label="Faith symbols around a person icon"></span></div>Faith Based<br>Organizations</div>
  <div class="abs org" style="left:718px;top:436px"><div class="org-ring"><span role="img" aria-label="Graduate in cap icon"></span></div>Colleges And<br>Universitie</div>
</section>

<section>
  <h2 class="abs center h2" style="top:906px">Our Process</h2>
  <div class="abs step" style="left:75px;top:1005px"><h3>Step 1</h3><p>Sed ut perspiciatis unde omnis iste natus error sit voluptatem accus antium enim ipsam.</p></div>
  <div class="abs step" style="left:75px;top:1253px"><h3>Step 2</h3><p>Sed ut perspiciatis unde omnis iste natus error sit voluptatem accus antium enim ipsam.</p></div>
  <div class="abs step" style="left:795px;top:1005px"><h3>Step 3</h3><p>Sed ut perspiciatis unde omnis iste natus error sit voluptatem accus antium enim ipsam.</p></div>
  <div class="abs step" style="left:795px;top:1253px"><h3>Step 4</h3><p>Sed ut perspiciatis unde omnis iste natus error sit voluptatem accus antium enim ipsam.</p></div>
  <svg class="abs" style="left:395px;top:990px" width="410" height="410" viewBox="0 0 410 410">
    <circle cx="205" cy="205" r="193" fill="var(--white)" stroke="var(--teal)" stroke-width="5"/>
    <polygon points="205,110 298,240 112,240" fill="var(--green)"/>
    <g fill="var(--white)" stroke="var(--teal)" stroke-width="4">
      <circle cx="20" cy="160" r="11"/><circle cx="20" cy="260" r="11"/><circle cx="390" cy="160" r="11"/><circle cx="390" cy="260" r="11"/>
    </g>
    <g font-family="Lexend,sans-serif" font-size="16" fill="#0d1b3a" text-anchor="middle">
      <text x="208" y="73">501c3</text><text x="205" y="94">ORGANIZATIONS</text>
      <text x="115" y="267">DATA</text><text x="115" y="287">OBJECT</text><text x="115" y="307">"DONOR"</text>
      <text x="295" y="263">DATA</text><text x="295" y="283">EXCHANGE</text><text x="295" y="303">"BUYER"</text>
    </g>
  </svg>
  <div class="btn" style="left:502px;top:1444px;width:196px;height:52px">Donate Plan</div>
</section>

<section>
  <svg class="abs" style="top:1570px;left:0" width="1200" height="130" viewBox="0 0 1200 130">
    <path d="M0 110 C150 20 300 20 450 70 C650 130 800 20 1000 10 C1100 5 1160 40 1200 70 L1200 130 L0 130Z" fill="var(--green)"/>
    <path d="M700 80 C850 10 1000 0 1100 30 C1150 45 1180 70 1200 90 L1200 130 L700 130Z" fill="#2a55c8"/>
    <path d="M0 130 C150 50 300 40 450 90 C650 150 820 40 1000 40 C1100 40 1160 80 1200 110 L1200 130Z" fill="var(--navy)"/>
  </svg>
  <div class="abs dark" style="top:1698px;left:0;width:1200px;height:710px"></div>
  <h2 class="abs center h2" style="top:1730px;color:var(--white)">My Donation</h2>
  <p class="abs center" style="top:1790px;font-size:31px;color:var(--white);font-weight:300">All donations are tax deductible</p>
  <p class="abs" style="left:108px;top:1928px;font-size:40px;color:var(--white);font-weight:300">I want to give</p>
  <div class="abs amount" style="left:422px;top:1870px">$25</div>
  <div class="abs amount" style="left:654px;top:1870px">$50</div>
  <div class="abs amount" style="left:886px;top:1870px">$100</div>
  <div class="abs amount" style="left:422px;top:1974px">$125</div>
  <div class="abs amount" style="left:654px;top:1974px">$150</div>
  <div class="abs amount" style="left:886px;top:1974px;font-size:22px">Other Amount</div>
  <div class="abs pay-box">
    <span class="pay-name">Paywise</span>
    <span class="card">Versa</span><span class="card">Mintcard</span><span class="card">Maxpay</span><span class="card">Amplex</span>
  </div>
  <div class="btn" style="left:459px;top:2274px;width:281px;height:52px">Donate With Credit Card</div>
</section>

<section>
  <div class="abs option" style="left:165px;top:2487px">
    <div class="ico" role="img" aria-label="Crypto coin network icon"></div>
    <div><h4>Donate with<br>Crypto</h4><small>powered by LLT</small><div class="mini"><i></i>Ledgerleaf</div></div>
  </div>
  <div class="btn" style="left:326px;top:2646px;width:194px;height:54px">Donate Now</div>
  <div class="abs option" style="left:617px;top:2487px">
    <div class="ico" role="img" aria-label="Database with gear icon"></div>
    <div><h4>Donate with<br>Data</h4></div>
  </div>
  <div class="btn" style="left:778px;top:2646px;width:194px;height:54px">Donate Now</div>
</section>

<section>
  <svg class="abs" style="top:2780px;left:0" width="1200" height="110" viewBox="0 0 1200 110">
    <path d="M0 60 C150 0 400 10 600 50 C800 90 1000 20 1200 40 L1200 110 L0 110Z" fill="var(--green)"/>
    <path d="M0 100 C150 40 400 40 600 80 C800 120 1000 50 1200 70 L1200 110 L0 110Z" fill="var(--navy)"/>
  </svg>
  <div class="abs dark" style="top:2888px;left:0;width:1200px;height:367px"></div>
  <div class="abs video" role="img" aria-label="Video still: man facing a digital network sphere surrounded by data icons"></div>
  <div class="abs play"><svg width="68" height="68" viewBox="0 0 68 68"><polygon points="26,18 50,34 26,50" fill="#fff"/></svg></div>
</section>

<section>
  <h2 class="abs center h2" style="top:3497px">Why Enroll!</h2>
  <p class="abs center" style="top:3580px;font-size:25px;color:var(--muted);font-weight:300">To get full access to all the features, start by creating an account.</p>
  <div class="abs feat" style="left:88px;top:3663px"><div class="feat-ring"><span role="img" aria-label="NFT drop icon"></span></div><h3>Drops</h3><p>Purchase NFTs that are directly<br>sold by top Creator</p></div>
  <div class="abs feat" style="left:450px;top:3663px"><div class="feat-ring"><span role="img" aria-label="Online marketplace cart icon"></span></div><h3>Marketplace</h3><p>Bid on and auction off rare<br>digital collectibles</p></div>
  <div class="abs feat" style="left:812px;top:3663px"><div class="feat-ring"><span role="img" aria-label="NFT gallery icon"></span></div><h3>My NFTs</h3><p>A digital gallery to showcase<br>your collection</p></div>
</section>

<section>
  <svg class="abs" style="top:4020px;left:0" width="1200" height="120" viewBox="0 0 1200 120">
    <path d="M0 70 C150 0 400 10 600 50 C800 90 1000 20 1200 40 L1200 120 L0 120Z" fill="var(--green)"/>
    <path d="M0 110 C150 40 400 40 600 80 C800 120 1000 50 1200 70 L1200 120 L0 120Z" fill="var(--navy)"/>
  </svg>
  <div class="abs dark" style="top:4138px;left:0;width:1200px;height:514px"></div>
  <h2 class="abs center" style="top:4216px;font-size:41px;color:var(--white);font-weight:400">Get Notified About New Amazing Products</h2>
  <p class="abs center" style="top:4287px;font-size:34px;color:var(--white);font-weight:300">Never Miss a Drop</p>
  <p class="abs center" style="top:4337px;font-size:25px;color:var(--white);font-weight:300">Subscribe for the latest news, drops &amp; collectibles</p>
  <div class="abs email"><span>Email Address</span></div>
  <div class="btn send">Send</div>
  <p class="abs center fine" style="top:4490px">After reading the Privacy Notice, you may subscribe for our newsletter to get special offers and occasional surveys<br>delivered to your inbox. Unsubscribe at any time by clicking on the link in the email.</p>
  <p class="abs center fine" style="top:4557px">&#9633; By entering my email and subscribing I confirm and agree to the above.</p>
</section>

<footer>
  <div class="abs footer"></div>
  <nav class="abs center foot-links"><span>HOME</span><span>ABOUT US</span><span>NEWSROOM</span><span>PATENTS</span><span>CLIENTS</span><span>FAQ</span><span>CONTACT</span></nav>
  <p class="abs center copy">Copyright © 2022 Company Name All Right reserved</p>
  <div class="abs center social"><span>Facenet</span><span>Pixgram</span><span>Chirper</span><span>Linkwork</span><span>Viewtube</span></div>
</footer>

</body>
</html>
```